Corvane Business Cards

Front of business card will have logo, name, address, & telephone number. Back of card will have a list of services provided - Roads, Substation Pads, Temporary Pads, Site Pads, Land Leveling, Powerline Row Cleaning, Land Clearing, Gates, Fencing, Construction Entrances, Excavation, Trenching, Underground Utilities, Directional Boring, Pile Driving. We are a construction company that uses heavy equipment like bulldozers, motor graders/blades, dump trucks, backhoes, hydro axes, & skid loaders. We build roads, pads, & install electric utility lines & waterlines underground. This logo is new. The word "Construction" can be smaller as uploaded 2 example edited logos. We will be using this card design for many employees.
Target Market(s)
Industrial Electric Powerline, Wind Turbine, Solar Panel, & Water Utility companies.
Contact Information for Business Card
Name/Position - Dwayne Halster - Owner
Address: 4875 FM 309
Calder Ridge, KS 66914
Phone number - (555) 482-5096

```html
<!DOCTYPE html>
<html lang="en">
<head>
<meta charset="UTF-8">
<title>Corvane Construction Business Cards</title>
<link rel="stylesheet" href="https://fonts.googleapis.com/css2?family=Poppins:wght@400;500;600&display=swap">
<style>
  :root {
    --page-bg: #9a9b9b;
    --card-light: #ebebed;
    --maroon: #3f0c15;
    --maroon-band: #3a0911;
    --ink: #3a2a2e;
    --rule: #8c5a63;
    --on-dark: #e6e1e2;
  }
  * { margin: 0; padding: 0; box-sizing: border-box; }
  html, body {
    width: 1105px;
    height: 1200px;
    overflow: hidden;
    background: var(--page-bg);
    font-family: "Poppins", sans-serif;
  }
  .card {
    position: absolute;
    left: 182px;
    width: 746px;
    height: 425px;
  }
  .card-front { top: 119px; background: var(--card-light); }
  .card-back { top: 637px; background: var(--maroon); }

  .brand-lockup {
    position: absolute;
    right: 42px;
    top: 64px;
    text-align: center;
    color: var(--maroon);
    font-weight: 600;
    line-height: 1;
  }
  .brand-name { font-size: 60px; letter-spacing: 1px; }
  .brand-sub { font-size: 22px; letter-spacing: 0.5px; margin-top: 14px; }

  .holder {
    position: absolute;
    left: 37px;
    top: 242px;
    color: var(--maroon);
  }
  .holder-name { font-size: 22px; font-weight: 600; line-height: 1.1; }
  .holder-role { font-size: 17px; font-weight: 400; color: var(--ink); line-height: 1.2; }

  .divider {
    position: absolute;
    left: 37px;
    right: 42px;
    top: 302px;
    height: 1px;
    background: var(--rule);
  }

  .contact-list {
    position: absolute;
    left: 37px;
    top: 317px;
    list-style: none;
    font-size: 18px;
    color: var(--ink);
    line-height: 22px;
  }
  .contact-list li { display: flex; align-items: center; gap: 8px; }
  .contact-list svg { width: 13px; height: 13px; fill: var(--maroon); }

  .address {
    position: absolute;
    right: 42px;
    top: 317px;
    text-align: right;
    font-size: 18px;
    color: var(--ink);
    line-height: 26px;
    font-style: normal;
  }

  .footer-band {
    position: absolute;
    left: 0;
    right: 0;
    top: 380px;
    height: 29px;
    background: var(--maroon-band);
    display: flex;
    align-items: center;
    justify-content: space-between;
    padding: 0 42px 0 37px;
    color: #f2eef0;
  }
  .footer-url { font-size: 17px; }
  .footer-brand { font-size: 13px; font-weight: 600; letter-spacing: 0.5px; }

  .back-brand {
    position: absolute;
    left: 0;
    right: 0;
    top: 140px;
    text-align: center;
    color: var(--on-dark);
    font-weight: 600;
    font-size: 92px;
    letter-spacing: 2px;
    line-height: 1;
  }
  .service-list {
    position: absolute;
    left: 0;
    right: 0;
    top: 340px;
    text-align: center;
    color: var(--on-dark);
    font-size: 16.5px;
    line-height: 20px;
  }
</style>
</head>
<body>
  <section class="card card-front">
    <div class="brand-lockup">
      <div class="brand-name">CORVANE</div>
      <div class="brand-sub">CONSTRUCTION</div>
    </div>

    <div class="holder">
      <div class="holder-name">DWAYNE HALSTER</div>
      <div class="holder-role">Owner</div>
    </div>

    <div class="divider"></div>

    <ul class="contact-list">
      <li>
        <svg viewBox="0 0 24 24" aria-hidden="true"><path d="M6.6 10.8a15.1 15.1 0 0 0 6.6 6.6l2.2-2.2a1 1 0 0 1 1-.25 11.4 11.4 0 0 0 3.6.57 1 1 0 0 1 1 1V20a1 1 0 0 1-1 1A17 17 0 0 1 3 4a1 1 0 0 1 1-1h3.5a1 1 0 0 1 1 1c0 1.25.2 2.45.57 3.57a1 1 0 0 1-.25 1z"/></svg>
        (555) 482-5096
      </li>
      <li>
        <svg viewBox="0 0 24 24" aria-hidden="true"><path d="M2 6.5V18a1 1 0 0 0 1 1h18a1 1 0 0 0 1-1V6.5l-10 6.5z"/><path d="M2.5 5h19L12 11.2z"/></svg>
        info@corvaneconstruction.com
      </li>
    </ul>

    <address class="address">4875 FM 309<br>Calder Ridge, KS 66914</address>

    <div class="footer-band">
      <span class="footer-url">www.corvaneconstruction.com</span>
      <span class="footer-brand">CORVANE</span>
    </div>
  </section>

  <section class="card card-back">
    <div class="back-brand">CORVANE</div>
    <p class="service-list">
      Roads • Substation Pads•Temporary Pads • Site Pads • Land Leveling<br>
      Powerline Row Cleaning • Land Clearing • Gates• Fencing • Construction Entrances<br>
      Excavation • Trenching • Underground Utilities• Directional Boring • Pile Driving
    </p>
  </section>
</body>
</html>
```